business card deign

Logo needs the following on it.
1. attached logo
2. Tagline - "If it chills a glass or fuels the fun...count on us!"
3. Name- Dalton Pikes, Founder and CPO
4. Address - 412 E. Carver Avenue, Ste 2207, Tampa, FL. 33917
5. Phone - 555.318.4726

```html
<!DOCTYPE html>
<html lang="en">
<head>
<meta charset="utf-8">
<title>Joeyline business card</title>
<link href="https://fonts.googleapis.com/css2?family=Montserrat:wght@400;500;700;800&display=swap" rel="stylesheet">
<style>
  :root {
    --stage: #e9e6e1;
    --ink: #111111;
    --paper: #ffffff;
    --night: #151515;
    --silver: #d9d9d9;
    --rule: #222222;
  }
  * { box-sizing: border-box; margin: 0; padding: 0; }
  html, body { width: 1200px; height: 931px; overflow: hidden; }
  body {
    background: var(--stage);
    font-family: "Montserrat", sans-serif;
    color: var(--ink);
    display: flex;
    flex-direction: column;
    align-items: center;
    justify-content: center;
    gap: 36px;
  }
  .card {
    width: 700px;
    height: 400px;
    position: relative;
    overflow: hidden;
    box-shadow: 0 6px 18px rgba(0,0,0,.18);
  }

  /* Back side */
  .card--back { background: var(--night); }
  .back-pattern {
    position: absolute; inset: 0;
    background: linear-gradient(105deg, var(--silver) 0%, #6d6d6d 22%, #2a2a2a 45%, var(--night) 70%);
    opacity: .55;
  }
  .back-brand {
    position: absolute; left: 0; right: 0; top: 50%;
    transform: translateY(-50%);
    display: flex; flex-direction: column; align-items: center; gap: 18px;
  }
  .brand-mark { width: 34px; height: 34px; border-radius: 50%; background: var(--paper); }
  .brand-name {
    font-weight: 800; font-size: 46px; letter-spacing: 14px;
    color: var(--paper); padding-left: 14px;
  }

  /* Front side */
  .card--front { background: var(--paper); }
  .front-brand {
    position: absolute; left: 60px; top: 90px; width: 250px; height: 190px;
    display: flex; flex-direction: column; align-items: center; justify-content: center; gap: 16px;
  }
  .front-brand .brand-mark { background: var(--ink); width: 30px; height: 30px; }
  .front-brand .brand-name { color: var(--ink); font-size: 32px; letter-spacing: 9px; padding-left: 9px; }
  .divider {
    position: absolute; left: 340px; top: 100px; width: 2px; height: 165px;
    background: var(--rule);
  }
  .contact { position: absolute; left: 370px; top: 96px; }
  .contact-name { font-weight: 800; font-size: 24px; letter-spacing: .5px; text-transform: uppercase; }
  .contact-role { font-weight: 400; font-size: 20px; margin-top: 2px; }
  .contact-lines { margin-top: 26px; font-size: 19px; line-height: 1.3; }
  .contact-line { display: flex; align-items: flex-start; gap: 10px; }
  .contact-line svg { width: 20px; height: 20px; flex: none; margin-top: 3px; }
  .tagline {
    position: absolute; left: 0; right: 0; bottom: 52px;
    text-align: center; font-size: 21px; font-weight: 500;
  }
</style>
</head>
<body>
  <section class="card card--back" aria-label="Card back">
    <div class="back-pattern" role="img" aria-label="Repeating pattern of small brand symbols fading from silver to black"></div>
    <div class="back-brand">
      <span class="brand-mark"></span>
      <span class="brand-name">JOEYLINE</span>
    </div>
  </section>

  <section class="card card--front" aria-label="Card front">
    <div class="front-brand">
      <span class="brand-mark"></span>
      <span class="brand-name">JOEYLINE</span>
    </div>
    <div class="divider"></div>
    <div class="contact">
      <p class="contact-name">Dalton Pikes</p>
      <p class="contact-role">Founder and CPO</p>
      <div class="contact-lines">
        <p class="contact-line">
          <svg viewBox="0 0 24 24" aria-hidden="true"><path fill="#111" d="M3 9c0-3 4-5 9-5s9 2 9 5v2h-4V9.5c-1.5-.6-3.2-.9-5-.9s-3.5.3-5 .9V11H3zm4 3h10l3 8H4z"/></svg>
          <span>555.318.4726</span>
        </p>
        <p class="contact-line">
          <svg viewBox="0 0 24 24" aria-hidden="true"><path fill="none" stroke="#111" stroke-width="2.4" d="M12 22s-7-7.5-7-12a7 7 0 0 1 14 0c0 4.5-7 12-7 12z"/><circle cx="12" cy="10" r="2.5" fill="#111"/></svg>
          <span>412 E. Carver Avenue, Ste<br>2207, Tampa, FL. 33917</span>
        </p>
      </div>
    </div>
    <p class="tagline">If it chills a glass or fuels the fun...count on us!</p>
  </section>
</body>
</html>
```